General contractor/GM consaltant business card

I need a card for my contracting company in North Dakota, we build industrial buildings for the oil feild and oil feild related companies offices, shops, airplain hangars, airports ext. We have a familly atmosphere on the job and are very relational and personal.
Industry/Entity Type
Industrial
Contact Information for Business Card
Ridgepost Contractors LLC.
Derek T.Holloway
4837 Tamarind dr. Colorado Springs, CO. 80917
Cell# 406-555-0148
derek@ridgepostcontractors.com

```html
<!DOCTYPE html>
<html lang="en">
<head>
<meta charset="utf-8">
<title>Ridgepost Contractors LLC. – Business Card</title>
<link href="https://fonts.googleapis.com/css2?family=Arimo:wght@400;700&family=Roboto:wght@300&display=swap" rel="stylesheet">
<style>
  :root {
    --bg: #e9e6e1;
    --deep-blue: #1f3f94;
    --violet: #6a4c9c;
    --rose: #c2456f;
    --crimson: #d52234;
    --ink: #ffffff;
    --shadow: rgba(40, 30, 20, 0.28);
  }
  * { margin: 0; padding: 0; box-sizing: border-box; }
  html, body {
    width: 1200px;
    height: 858px;
    overflow: hidden;
    background: var(--bg);
  }
  .sheet {
    width: 1200px;
    height: 858px;
    display: flex;
    align-items: center;
    justify-content: center;
    gap: 28px;
  }
  .card {
    position: relative;
    width: 560px;
    height: 320px;
    border-radius: 3px;
    color: var(--ink);
    box-shadow: 0 10px 24px var(--shadow);
    overflow: hidden;
  }
  .card--front {
    background: linear-gradient(150deg, var(--deep-blue) 0%, var(--violet) 30%, var(--rose) 55%, var(--crimson) 100%);
  }
  .card--back {
    background: linear-gradient(330deg, var(--deep-blue) 0%, var(--violet) 30%, var(--rose) 55%, var(--crimson) 100%);
    display: flex;
    align-items: center;
    justify-content: center;
  }
  .brand {
    display: flex;
    align-items: center;
    gap: 12px;
    font-family: "Arimo", Arial, sans-serif;
    font-weight: 700;
    color: var(--ink);
    white-space: nowrap;
  }
  .brand__mark {
    width: 16px;
    height: 16px;
    border-radius: 50%;
    background: var(--ink);
    flex: none;
  }
  .card--front .brand {
    position: absolute;
    left: 40px;
    top: 46px;
    font-size: 30px;
  }
  .card--back .brand {
    font-size: 32px;
  }
  .contact {
    position: absolute;
    left: 150px;
    top: 132px;
    font-family: "Roboto", "Helvetica Neue", Arial, sans-serif;
    font-weight: 300;
  }
  .contact__name {
    font-size: 27px;
    letter-spacing: 0.2px;
    margin-bottom: 14px;
  }
  .contact__line {
    font-size: 15px;
    line-height: 22px;
  }
</style>
</head>
<body>
  <main class="sheet">
    <section class="card card--front" aria-label="Business card front">
      <div class="brand">
        <span class="brand__mark"></span>
        <span class="brand__name">Ridgepost Contractors LLC.</span>
      </div>
      <div class="contact">
        <p class="contact__name">Derek T.Holloway</p>
        <p class="contact__line">406-555-0148</p>
        <p class="contact__line">derek@ridgepostcontractors.com</p>
        <p class="contact__line">4837 Tamarind dr.</p>
        <p class="contact__line">Colorado Springs, CO. 80917</p>
      </div>
    </section>
    <section class="card card--back" aria-label="Business card back">
      <div class="brand">
        <span class="brand__mark"></span>
        <span class="brand__name">Ridgepost Contractors LLC.</span>
      </div>
    </section>
  </main>
</body>
</html>
```